Corporate Business Card

Very professional, Modern, Not to busy, include phone address email, website
(253) 617-4930, 18761 52nd Avenue S, Kent, WA 98047, martin@plumlinegroup.com, varkoworks.com

Target Market(s)

Manufacturing

Industry/Entity Type

Aero, machining, manufacturing, Off road racing

Contact Information for Business Card

Phone, address email, website

```html
<!DOCTYPE html>
<html lang="en">
<head>
<meta charset="utf-8">
<title>Varko Works — Business Card</title>
<link rel="stylesheet" href="https://fonts.googleapis.com/css2?family=Orbitron:wght@700&family=Roboto:wght@400;700&display=swap">
<style>
  :root {
    --backdrop: #2b2b2b;
    --card-top: #2c3a6c;
    --card-bottom: #25315d;
    --pattern-light: #34447a;
    --pattern-dark: #1f2a52;
    --ink-light: #eceef3;
    --accent-red: #c8242b;
    --rule: #e6e8ee;
  }
  * { box-sizing: border-box; margin: 0; padding: 0; }
  html, body {
    width: 1200px;
    height: 1138px;
    overflow: hidden;
    background: var(--backdrop);
  }
  .canvas {
    position: relative;
    width: 1200px;
    height: 1138px;
  }
  .card {
    position: absolute;
    border-radius: 16px;
    overflow: hidden;
    background: linear-gradient(180deg, var(--card-top), var(--card-bottom));
    box-shadow: 0 6px 14px rgba(0,0,0,0.45);
  }
  .card--front { left: 274px; top: 186px; width: 623px; height: 376px; }
  .card--back  { left: 276px; top: 608px; width: 618px; height: 374px; }

  .front__pattern {
    position: absolute;
    inset: 0;
    background:
      linear-gradient(120deg, var(--pattern-dark) 0%, var(--pattern-light) 55%, var(--card-bottom) 100%);
  }
  .brand {
    position: absolute;
    left: 54px;
    top: 272px;
    font-family: "Roboto", sans-serif;
    font-weight: 700;
    font-size: 36px;
    letter-spacing: 1px;
    color: var(--ink-light);
    white-space: nowrap;
  }
  .brand__rule {
    position: absolute;
    left: 50px;
    top: 333px;
    width: 104px;
    height: 2px;
    background: var(--rule);
  }

  .contact {
    position: absolute;
    left: 0;
    right: 0;
    top: 114px;
    text-align: center;
    color: var(--ink-light);
    font-family: "Roboto", sans-serif;
  }
  .contact__name {
    font-family: "Orbitron", sans-serif;
    font-weight: 700;
    font-size: 29px;
    letter-spacing: 0.5px;
    line-height: 1;
    margin-bottom: 13px;
  }
  .contact__name-last { color: var(--accent-red); }
  .contact__line {
    font-size: 16.5px;
    line-height: 24.5px;
  }
  .contact__line--address { margin-top: 8px; }
</style>
</head>
<body>
  <main class="canvas">
    <section class="card card--front" aria-label="Card front">
      <div class="front__pattern" role="img" aria-label="Tone-on-tone embossed repeating brand pattern in navy"></div>
      <div class="brand">Varko Works</div>
      <div class="brand__rule"></div>
    </section>

    <section class="card card--back" aria-label="Card back">
      <div class="contact">
        <h1 class="contact__name">MARTIN <span class="contact__name-last">CALDER</span></h1>
        <p class="contact__line">(253) 617-4930</p>
        <p class="contact__line">martin@plumlinegroup.com</p>
        <p class="contact__line">www.varkoworks.com</p>
        <p class="contact__line contact__line--address">18761 52nd Avenue S, Kent, WA 98047</p>
      </div>
    </section>
  </main>
</body>
</html>
```